Alterations to existing business card

Here is my current logo and I want the "cafe and bar" taken off with just the words Lumo and our slogan "Savour the Moment" on the card, Plus the logo.
Our Current Business Card is currently 5.5cm by 5.5cm and would like it to remain like this thanks.
The loyalty card can be 10 squares with the logo specifying the 10th coffee free. I would like the cheapest option please.
Also on our business card would like the Facebook logo and instagram Logo with TAZALUMO27 as link to our photos on instagram.

Keep Colour schemes the same please.

On the business cards

Dale Brinton Director
0427916038
dale27lumo@mailvista.test

Paula Ferrisi Principal
0428571963
paulumo@mailvista.test

Thanks Dale

Industry/Entity Type

Business

```html
<!DOCTYPE html>
<html lang="en">
<head>
<meta charset="utf-8">
<title>Lumo – Business Card and Loyalty Card</title>
<link rel="stylesheet" href="https://fonts.googleapis.com/css2?family=Questrial&family=Montserrat:wght@700&display=swap">
<style>
  :root {
    --backdrop: #4b4b4b;
    --paper: #ffffff;
    --ink: #111111;
    --gold: #e9a531;
    --gold-deep: #d9952a;
    --gold-light: #f7dc72;
    --band: #050505;
    --band-text: #ffffff;
  }
  * { margin: 0; padding: 0; box-sizing: border-box; }
  html, body { width: 1105px; height: 1200px; overflow: hidden; }
  body {
    position: relative;
    background: var(--backdrop);
    font-family: "Questrial", "Century Gothic", sans-serif;
  }

  /* Business card */
  .business-card {
    position: absolute; left: 124px; top: 110px;
    width: 449px; height: 449px;
    background: var(--paper);
  }
  .brand-seal {
    position: absolute; left: 53px; top: 24px;
    width: 138px; height: 138px; border-radius: 50%;
    border: 3px solid var(--gold);
    display: flex; align-items: center; justify-content: center;
    color: var(--gold); font-size: 34px; letter-spacing: 2px;
  }
  .brand-name {
    position: absolute; left: 28px; top: 184px;
    font-size: 62px; line-height: 1; letter-spacing: 3px; color: var(--ink);
  }
  .brand-slogan {
    position: absolute; left: 30px; top: 246px;
    font-size: 13px; letter-spacing: 1.6px; color: var(--gold);
    font-style: italic; white-space: nowrap;
  }
  .person-name {
    position: absolute; left: 30px; top: 274px;
    font-size: 28px; letter-spacing: 0.8px; color: var(--gold);
    white-space: nowrap;
  }
  .person-role {
    position: absolute; left: 32px; top: 312px;
    font-size: 19px; color: var(--ink);
  }
  .contact-band {
    position: absolute; left: 0; top: 356px;
    width: 366px; height: 93px; background: var(--band);
    padding: 20px 0 0 32px;
  }
  .contact-line {
    display: flex; align-items: center; gap: 14px;
    color: var(--band-text); font-size: 20px; height: 29px;
    white-space: nowrap;
  }
  .contact-line svg { width: 16px; height: 18px; flex: none; }
  .corner-mark {
    position: absolute; left: 366px; top: 356px;
    width: 83px; height: 93px;
    display: flex; align-items: center; justify-content: center;
    color: var(--gold); font-size: 18px; letter-spacing: 1px;
  }

  /* Loyalty card */
  .loyalty-card {
    position: absolute; left: 500px; top: 628px;
    width: 447px; height: 447px;
    background: linear-gradient(90deg, var(--gold-deep) 0%, var(--gold) 45%, var(--gold-light) 100%);
  }
  .loyalty-seal {
    position: absolute; left: 135px; top: 21px;
    width: 166px; height: 166px; border-radius: 50%;
    border: 4px solid var(--ink);
    display: flex; align-items: center; justify-content: center;
    font-size: 40px; letter-spacing: 2px; color: var(--ink);
  }
  .stamp-grid {
    position: absolute; left: 34px; top: 221px;
    display: grid; grid-template-columns: repeat(5, 64px);
    column-gap: 11px; row-gap: 23px;
  }
  .stamp {
    width: 64px; height: 64px; border-radius: 50%;
    border: 3px solid var(--ink);
    display: flex; align-items: center; justify-content: center;
  }
  .stamp svg { width: 38px; height: 34px; }
  .stamp--free {
    background: var(--gold-deep);
    font-family: "Montserrat", sans-serif; font-weight: 700;
    font-size: 17px; color: var(--ink);
  }
  .social-row {
    position: absolute; left: 40px; top: 397px; width: 367px;
    display: flex; align-items: center; gap: 8px;
    font-size: 19px; letter-spacing: 1px; color: var(--ink);
  }
  .social-row .rule { flex: 1; height: 1px; background: var(--ink); }
  .social-dot { width: 18px; height: 18px; border-radius: 50%; background: var(--ink); flex: none; }
</style>
</head>
<body>
  <svg width="0" height="0" style="position:absolute" aria-hidden="true">
    <defs>
      <symbol id="cup-icon" viewBox="0 0 38 34">
        <path d="M14 2c-2 2 2 4 0 7M19 1c-2 2 2 4 0 7M24 2c-2 2 2 4 0 7" fill="none" stroke="#111" stroke-width="1.6" stroke-linecap="round"/>
        <path d="M6 13h24v6a10 10 0 0 1-10 10h-4a10 10 0 0 1-10-10z" fill="#111"/>
        <path d="M30 15h2a4 4 0 0 1 0 8h-3" fill="none" stroke="#111" stroke-width="2.4"/>
        <rect x="2" y="30" width="32" height="3" rx="1.5" fill="#111"/>
      </symbol>
    </defs>
  </svg>

  <section class="business-card" aria-label="Business card">
    <div class="brand-seal">LUMO</div>
    <div class="brand-name">LUMO</div>
    <div class="brand-slogan">SAVOUR THE MOMENT</div>
    <div class="person-name">DALE BRINTON</div>
    <div class="person-role">DIRECTOR</div>
    <div class="contact-band">
      <div class="contact-line">
        <svg viewBox="0 0 16 18" aria-hidden="true"><rect x="3" y="0.8" width="10" height="16.4" rx="1.8" fill="none" stroke="#e9a531" stroke-width="1.6"/><circle cx="8" cy="14" r="1" fill="#e9a531"/></svg>
        <span>0427916038</span>
      </div>
      <div class="contact-line">
        <svg viewBox="0 0 16 18" aria-hidden="true"><rect x="0.5" y="4" width="15" height="10" fill="#e9a531"/><path d="M0.5 4l7.5 6 7.5-6" fill="none" stroke="#050505" stroke-width="1.3"/></svg>
        <span>dale27lumo@mailvista.test</span>
      </div>
    </div>
    <div class="corner-mark">LUMO</div>
  </section>

  <section class="loyalty-card" aria-label="Loyalty card">
    <div class="loyalty-seal">LUMO</div>
    <div class="stamp-grid">
      <div class="stamp"><svg><use href="#cup-icon"/></svg></div>
      <div class="stamp"><svg><use href="#cup-icon"/></svg></div>
      <div class="stamp"><svg><use href="#cup-icon"/></svg></div>
      <div class="stamp"><svg><use href="#cup-icon"/></svg></div>
      <div class="stamp"><svg><use href="#cup-icon"/></svg></div>
      <div class="stamp"><svg><use href="#cup-icon"/></svg></div>
      <div class="stamp"><svg><use href="#cup-icon"/></svg></div>
      <div class="stamp"><svg><use href="#cup-icon"/></svg></div>
      <div class="stamp"><svg><use href="#cup-icon"/></svg></div>
      <div class="stamp stamp--free">FREE</div>
    </div>
    <div class="social-row">
      <span class="rule"></span>
      <span class="social-dot"></span>
      <span class="social-dot"></span>
      <span>TAZALUMO27</span>
      <span class="rule"></span>
    </div>
  </section>
</body>
</html>
```